Coffee House With Cycling Theme Wants Business Cards

We want to create a business card for a coffee house that has a cycling theme. We expect to use the current logo on one side of the business card and we have been considering adding the words 'COFFEE HOUSE' underneath (see example). For the other side of the business card we want an interesting design with tag-line, address and social media links (the normal business card stuff). See examples provided but we are not fixed on having it exactly as shown, we are very open to great creative ideas. Please note our logo has the initials ‘KR' in orange embedded in the design and this must be retained. However, you can play with the words COFFEE HOUSE as well as use the orange color on the backside of the business card, as you see fit. For an image on the backside of the business card it can be a photo, hand-drawn or whatever but it must visually combine coffee and cycling in some way. The interior of the Coffee House will be reclaimed wood, rustic and have an urban feel to it with cycling artifacts hanging from the walls/ceiling, etc. Finally, it would be beneficial if the business card design elements can be easily used on flyers and other promotional assets. Good luck, we are looking forward to seeing your creative ideas.

Target Market(s)

Coffee lovers and cycling fans

Contact Information for Business Card

See project description.

Colors

Designer to choose colors to be used in the design.

Requirements
Must have
• Must use the current logo provided and combine a coffee and bike theme.
Nice to have
• Orange is used in current logo and could be used as an accent color on the backside of the business card.

```html
<!DOCTYPE html>
<html lang="en">
<head>
<meta charset="utf-8">
<title>KR Coffee House — Business Card</title>
<link rel="stylesheet" href="https://fonts.googleapis.com/css2?family=Montserrat:wght@400;800&display=swap">
<style>
  :root {
    --backdrop: #c8c8ca;
    --card-white: #ffffff;
    --charcoal: #363a3e;
    --ink: #1d1f21;
    --accent-orange: #ec6a1f;
  }
  * { box-sizing: border-box; margin: 0; padding: 0; }
  html, body {
    width: 1200px;
    height: 799px;
    overflow: hidden;
    background: var(--backdrop);
    font-family: "Montserrat", sans-serif;
  }
  .stage {
    position: relative;
    width: 1200px;
    height: 799px;
  }
  .card {
    position: absolute;
    width: 540px;
    height: 309px;
    background: var(--card-white);
    overflow: hidden;
    box-shadow: 0 4px 14px rgba(0,0,0,0.18);
  }
  .card--front { left: 40px; top: 245px; }
  .card--back  { left: 620px; top: 245px; }

  .front-band {
    position: absolute;
    left: 0; right: 0;
    top: 72px;
    height: 172px;
    background: var(--charcoal);
    display: flex;
    align-items: center;
    justify-content: center;
  }

  .wordmark {
    display: flex;
    flex-direction: column;
    align-items: center;
    color: var(--card-white);
    font-weight: 800;
    line-height: 1;
    letter-spacing: 0.5px;
  }
  .wordmark__row {
    display: flex;
    align-items: center;
    gap: 10px;
  }
  .wordmark__dot {
    width: 26px;
    height: 26px;
    border-radius: 50%;
    background: var(--accent-orange);
  }
  .wordmark__initials { font-size: 40px; }
  .wordmark__name { font-size: 27px; margin-top: 6px; }

  .back-art {
    position: absolute;
    inset: 0;
    width: 100%;
    height: 100%;
  }
  .back-logo {
    position: absolute;
    left: 0;
    top: 122px;
    width: 240px;
  }
  .back-logo .wordmark__initials { font-size: 36px; }
  .back-logo .wordmark__name { font-size: 24px; }
  .back-logo .wordmark__dot { width: 23px; height: 23px; }
  .contact-text {
    font-family: "Montserrat", sans-serif;
    font-size: 14px;
    font-weight: 400;
    fill: var(--ink);
  }
</style>
</head>
<body>
<main class="stage">

  <section class="card card--front" aria-label="Business card front">
    <div class="front-band">
      <div class="wordmark">
        <div class="wordmark__row">
          <span class="wordmark__dot"></span>
          <span class="wordmark__initials">KR</span>
        </div>
        <span class="wordmark__name">COFFEE HOUSE</span>
      </div>
    </div>
  </section>

  <section class="card card--back" aria-label="Business card back">
    <svg class="back-art" viewBox="0 0 540 309" xmlns="http://www.w3.org/2000/svg">
      <circle cx="100" cy="165" r="175" fill="var(--charcoal)"/>
      <path d="M242 25 A182 182 0 0 1 252.3 285" fill="none" stroke="var(--ink)" stroke-width="1.6"/>
      <circle cx="242" cy="25" r="3.5" fill="var(--ink)"/>
      <circle cx="252.3" cy="285" r="3.5" fill="var(--ink)"/>

      <g class="contact-icons" stroke="var(--ink)" stroke-width="2.5" fill="var(--card-white)">
        <circle cx="272" cy="60" r="13"/>
        <circle cx="293.5" cy="105" r="13"/>
        <circle cx="301.7" cy="150" r="13"/>
        <circle cx="298.6" cy="195" r="13"/>
        <circle cx="283.5" cy="240" r="13"/>
      </g>

      <circle class="icon-social" cx="272" cy="60" r="5.5" fill="var(--ink)"/>
      <circle class="icon-social" cx="293.5" cy="105" r="5.5" fill="var(--ink)"/>

      <g class="icon-mail" fill="none" stroke="var(--ink)" stroke-width="1.6">
        <rect x="294.7" y="145" width="14" height="10" rx="1"/>
        <path d="M294.7 145 L301.7 151 L308.7 145"/>
      </g>
      <g class="icon-web" fill="none" stroke="var(--ink)" stroke-width="1.4">
        <circle cx="298.6" cy="195" r="7"/>
        <ellipse cx="298.6" cy="195" rx="3" ry="7"/>
        <path d="M291.6 195 H305.6"/>
      </g>
      <path class="icon-pin" d="M283.5 232 a5.5 5.5 0 0 1 5.5 5.5 c0 4 -5.5 10 -5.5 10 s-5.5 -6 -5.5 -10 a5.5 5.5 0 0 1 5.5 -5.5 z" fill="var(--ink)"/>
      <circle cx="283.5" cy="237.5" r="2" fill="var(--card-white)"/>

      <text class="contact-text" x="295" y="65">krcoffeehouse</text>
      <text class="contact-text" x="316" y="110">krcoffeehouse</text>
      <text class="contact-text" x="324" y="155">info@krcoffeehouse.com</text>
      <text class="contact-text" x="321" y="200">www.krcoffeehouse.com</text>
      <text class="contact-text" x="306" y="245">Maple Square, Rowanford</text>
    </svg>

    <div class="back-logo">
      <div class="wordmark">
        <div class="wordmark__row">
          <span class="wordmark__dot"></span>
          <span class="wordmark__initials">KR</span>
        </div>
        <span class="wordmark__name">COFFEE HOUSE</span>
      </div>
    </div>
  </section>

</main>
</body>
</html>
```